Business Card Design for Vintage Jazz

I am a vintage jazz band leader in New York City. My groups play the music of the 1920s, 1930s and 1940s. My website is morvalquist.com for more info on what I do.

I am looking for a two sided business card design that has the look and feel of a really nice business card from the 1930s. I need to convey with the design that my work has that vintage kind of class and style, but also conveys that we are fun and entertaining.

Most importantly it should make a bold staement. If Hal Denbrook had a card, what would it have looked like? I want a card that I feel confident will make an impact and will let people know that my work is te the top that NYC has to offer in vintage jazz..

Note that I have only decided to avoid the "committed payment" option as I have not used this service before. Assuming that I get quality work I will select a design from those presented.

Target Market(s)

people who want to hire my band for events, media, and new fans of the band

Industry/Entity Type

Performing Art

Contact Information for Business Card

Definitely a matte finish, possibly a sort of old style of paper with that brown tint? definitely a thick card.

Requirements
Must have
• FRONT
• My name: Tobin Vashley
• What I do: Bandleader, Guitarist, Vocalist, Songwriter
• Contact Details: morvalquist.com tobin@morvalquist.com 646-555-0148
• BACK
• My Social Media Links:
• facebook.morvalquist.com
• twitter, instagram, linkedin: morvalquist
• I'm also including a photo image I would like to use. The photo's background is not needed, and to be honest isn't really desireable. Just looking to use the image of me.
Nice to have
• I'm attaching which could be used as is, omitted from the card, or altered maybe with text going around the outside of the circle or in some other way. It may need some clean up to the edges of the lettering as we only use it for the website thumbnail.
• If there's space I'd like to include the text "join our mailing list for a free song download: freesong.morvalquist.com" If not perhaps just "Download a Free Song at: freesong.morvalquist.com - something to this end.
Should not have
• anything cartoony. Don't think retro 90s's vision of the swing era, think actual swing era!
• anything modern. Got to look old school
• Try to avoid dark backgrounds. Since we often play in bars and clubs where it is dar, a d
• avoid script fonts.

```html
<!DOCTYPE html>
<html lang="en">
<head>
<meta charset="utf-8">
<title>Tobin Vashley – Business Cards</title>
<link rel="stylesheet" href="https://fonts.googleapis.com/css2?family=Josefin+Sans:wght@400;600;700&display=swap">
<style>
  :root {
    --backdrop: #2c2e33;
    --paper: #f6efdd;
    --ink: #1d1812;
    --rule: #6b5637;
    --shadow: rgba(0, 0, 0, 0.45);
  }
  * { box-sizing: border-box; margin: 0; padding: 0; }
  html, body {
    width: 1200px;
    height: 864px;
    overflow: hidden;
    background: var(--backdrop);
    font-family: "Josefin Sans", "Futura", Arial, sans-serif;
    color: var(--ink);
  }
  .canvas {
    position: relative;
    width: 1200px;
    height: 864px;
  }
  .card {
    position: absolute;
    width: 580px;
    height: 320px;
    background: var(--paper);
    box-shadow: 0 10px 24px var(--shadow);
  }
  .card__frame {
    position: absolute;
    inset: 14px;
    border: 3px double var(--rule);
    pointer-events: none;
  }
  .card--social { left: 200px; top: 60px; }
  .card--contact { left: 270px; top: 440px; }

  /* Social side */
  .social__name {
    position: absolute;
    top: 80px;
    width: 100%;
    text-align: center;
    font-size: 34px;
    font-weight: 700;
    letter-spacing: 1px;
  }
  .social__links {
    position: absolute;
    top: 176px;
    left: 0;
    width: 100%;
    display: flex;
    justify-content: center;
    gap: 44px;
    font-size: 14px;
  }
  .social__column { display: flex; flex-direction: column; gap: 4px; }
  .social__column--left { align-items: flex-end; }
  .social__item { display: flex; align-items: center; gap: 7px; line-height: 16px; }
  .social__mark {
    width: 11px;
    height: 11px;
    background: var(--ink);
    border-radius: 50%;
  }
  .social__role {
    position: absolute;
    top: 236px;
    width: 100%;
    text-align: center;
    font-size: 14px;
    font-weight: 700;
    letter-spacing: 0.6px;
  }

  /* Contact side */
  .contact {
    position: absolute;
    top: 74px;
    width: 100%;
    text-align: center;
  }
  .contact__name {
    font-size: 22px;
    font-weight: 700;
    letter-spacing: 1.5px;
    margin-bottom: 14px;
  }
  .contact__details {
    list-style: none;
    font-size: 15px;
    line-height: 1.3;
  }
  .contact__label { font-weight: 700; }
  .contact__role {
    margin-top: 18px;
    font-size: 16px;
    font-weight: 700;
    letter-spacing: 0.8px;
    line-height: 1.3;
  }
</style>
</head>
<body>
<main class="canvas">
  <section class="card card--social" aria-label="Card side with social links">
    <div class="card__frame" aria-hidden="true"></div>
    <h1 class="social__name">Tobin Vashley</h1>
    <div class="social__links">
      <div class="social__column social__column--left">
        <span class="social__item">morvalquist.com <span class="social__mark" aria-hidden="true"></span></span>
        <span class="social__item">morvalquist <span class="social__mark" aria-hidden="true"></span></span>
      </div>
      <div class="social__column">
        <span class="social__item"><span class="social__mark" aria-hidden="true"></span> morvalquist</span>
        <span class="social__item"><span class="social__mark" aria-hidden="true"></span> morvalquist</span>
      </div>
    </div>
    <p class="social__role">BANDLEADER, GUITARIST, VOCALIST, SONGWRITER</p>
  </section>

  <section class="card card--contact" aria-label="Card side with contact details">
    <div class="card__frame" aria-hidden="true"></div>
    <div class="contact">
      <h2 class="contact__name">TOBIN VASHLEY</h2>
      <ul class="contact__details">
        <li><span class="contact__label">Phone:</span> 646-555-0148</li>
        <li><span class="contact__label">Email:</span> tobin@morvalquist.com</li>
        <li><span class="contact__label">Website:</span> morvalquist.com</li>
      </ul>
      <p class="contact__role">BANDLEADER, GUITARIST,<br>VOCALIST, SONGWRITER</p>
    </div>
  </section>
</main>
</body>
</html>
```